Restaurant Facility Equipment & Store Maintenance/

I need a flyer showing commercial/industrial kitchen equipment photos we work on Hot Equipment & Cold Equipment and offer many services. see attached highlights

```html
<!DOCTYPE html>
<html lang="en">
<head>
<meta charset="utf-8">
<title>Restaurant Facility Equipment &amp; Store Maintenance</title>
<link rel="stylesheet" href="https://fonts.googleapis.com/css2?family=Montserrat:wght@800;900&family=Poppins:wght@600;700&family=Questrial&family=Oswald:wght@500;600&display=swap">
<style>
  :root {
    --blue: #1b61a3;
    --yellow: #f7d31c;
    --red: #e3191f;
    --red-dark: #a8121a;
    --cyan: #1fa3d9;
    --ink: #1d1d1f;
    --white: #ffffff;
    --page: #ffffff;
  }
  * { margin: 0; padding: 0; box-sizing: border-box; }
  html, body { width: 1103px; height: 1200px; overflow: hidden; background: var(--page); }
  .stage { width: 1500px; height: 1630px; transform: scale(0.73533); transform-origin: 0 0; position: relative; }
  .flyer {
    position: absolute; left: 220px; top: 130px; width: 1060px; height: 1372px;
    background: var(--white); overflow: hidden;
    box-shadow: 0 6px 26px rgba(0,0,0,.18);
    font-family: "Questrial", sans-serif; color: var(--ink);
  }
  .abs { position: absolute; }
  .hero-band { left: 0; top: 0; width: 1060px; height: 457px; background: var(--blue); }
  .hero-ring { left: 650px; top: -40px; width: 420px; height: 430px; border-radius: 50%; background: var(--white); }
  .hero-photo {
    left: 663px; top: 10px; width: 392px; height: 390px; border-radius: 50%;
    background: radial-gradient(circle at 40% 35%, #e6e9ec 0%, #b9bfc5 45%, #7e868e 100%);
  }
  .title { left: 55px; top: 58px; font-family: "Montserrat", sans-serif; font-weight: 900; font-size: 42.5px; line-height: 41px; color: var(--white); letter-spacing: -0.2px; }
  .title .hl { color: var(--yellow); display: block; }
  .subtitle { left: 54px; top: 184px; font-size: 31.5px; line-height: 29px; color: var(--white); }
  .rule { left: 63px; top: 269px; width: 572px; height: 2px; background: var(--yellow); opacity: .85; }
  .tagline { left: 54px; top: 296px; font-family: "Poppins", sans-serif; font-weight: 700; font-size: 30.5px; line-height: 37px; color: var(--white); }
  .hero-list { list-style: none; font-family: "Poppins", sans-serif; font-weight: 600; font-size: 19px; line-height: 25px; color: var(--white); }
  .hero-list li { display: flex; align-items: center; gap: 10px; }
  .hero-list.left { left: 56px; top: 382px; }
  .hero-list.right { left: 220px; top: 382px; text-transform: uppercase; }
  .tick { width: 20px; height: 20px; flex: none; }
  .equip-fold { left: 510px; top: 423px; width: 0; height: 0; border-left: 20px solid transparent; border-bottom: 34px solid var(--red-dark); }
  .equip-box {
    left: 530px; top: 423px; width: 485px; height: 302px; background: var(--red);
    border-radius: 0 0 30px 30px; color: var(--white); padding: 18px 0 0 48px;
  }
  .equip-box h2 { font-family: "Poppins", sans-serif; font-weight: 700; font-size: 21px; margin-bottom: 14px; }
  .equip-list { list-style: none; margin-left: -12px; font-size: 17px; }
  .equip-list li { display: flex; align-items: center; gap: 14px; height: 37.5px; }
  .section-title { font-family: "Poppins", sans-serif; font-weight: 700; font-size: 29px; color: var(--blue); }
  .section-title .accent { color: var(--red); }
  .support-title { left: 55px; top: 486px; }
  .check-list { list-style: none; font-size: 17px; line-height: 19px; }
  .check-list li { display: flex; align-items: flex-start; gap: 11px; }
  .support-list { left: 55px; top: 539px; }
  .support-list li { height: 37.4px; }
  .badge-plain { background: #dfe3e8; border-radius: 8px; }
  .badge-a { left: 538px; top: 752px; width: 182px; height: 58px; border-radius: 29px; }
  .badge-b { left: 786px; top: 744px; width: 216px; height: 73px; border: 4px solid var(--red-dark); background: #f4f4f4; }
  .photo { top: 884px; width: 296px; height: 198px; border: 2px solid var(--red); border-radius: 8px; }
  .photo-fryers { left: 55px; background: linear-gradient(135deg, #8c8678 0%, #5a554b 55%, #3d3a34 100%); }
  .photo-chefs { left: 395px; background: linear-gradient(135deg, #4c4c4e 0%, #2a2a2c 60%, #8a8a8c 100%); }
  .worker {
    left: 810px; top: 825px; width: 240px; height: 547px;
    background: linear-gradient(180deg, #2a5fb8 0%, #2450a6 55%, #c59a55 72%, #2450a6 82%);
    border-radius: 110px 110px 0 0; opacity: .95;
  }
  .why-title { left: 55px; top: 1095px; }
  .why-list { top: 1148px; }
  .why-list li { margin-bottom: 18px; }
  .why-list.left { left: 58px; }
  .why-list.right { left: 374px; }
  .footer-call { left: 58px; top: 1276px; }
  .call-label { font-family: "Oswald", sans-serif; font-weight: 500; font-size: 11.5px; color: var(--red); letter-spacing: -.2px; }
  .call-number { display: flex; align-items: center; gap: 6px; font-family: "Oswald", sans-serif; font-weight: 500; font-size: 24px; line-height: 32px; color: var(--ink); }
  .divider { top: 1275px; width: 1px; height: 48px; background: #9a9a9a; }
  .divider.one { left: 277px; }
  .divider.two { left: 518px; }
  .fix-all { left: 295px; top: 1274px; font-family: "Oswald", sans-serif; }
  .fix-all strong { display: block; font-weight: 600; font-size: 26px; line-height: 32px; color: var(--red); letter-spacing: -.4px; }
  .fix-all span { display: block; font-weight: 500; font-size: 15px; line-height: 17px; color: var(--ink); letter-spacing: -.3px; }
  .contact { left: 533px; top: 1275px; list-style: none; font-size: 19.5px; line-height: 25px; }
  .contact li { display: flex; align-items: center; gap: 9px; }
</style>
</head>
<body>
<svg width="0" height="0" style="position:absolute">
  <symbol id="tick-red" viewBox="0 0 20 20"><circle cx="10" cy="10" r="9.5" fill="#e3191f"/><path d="M5.5 10.3l3 3 6-6.3" fill="none" stroke="#fff" stroke-width="2.2" stroke-linecap="round" stroke-linejoin="round"/></symbol>
  <symbol id="tick-cyan" viewBox="0 0 20 20"><circle cx="10" cy="10" r="9.5" fill="#1fa3d9"/><path d="M5.5 10.3l3 3 6-6.3" fill="none" stroke="#fff" stroke-width="2.2" stroke-linecap="round" stroke-linejoin="round"/></symbol>
</svg>
<div class="stage">
  <div class="flyer">
    <div class="abs hero-band"></div>
    <div class="abs hero-ring"></div>
    <div class="abs hero-photo" role="img" aria-label="Photo of a stainless steel commercial kitchen line"></div>

    <h1 class="abs title">RESTAURANT<span class="hl">FACILITY EQUIPMENT</span><span class="hl">&amp; STORE MAINTENANCE</span></h1>
    <p class="abs subtitle">Commercial &amp; Industrial Kitchen Services<br>Denver Metro &amp; Surrounding Areas</p>
    <div class="abs rule"></div>
    <p class="abs tagline">We Handle Everything From<br>the Front Door to the Back Door</p>
    <ul class="abs hero-list left">
      <li><svg class="tick"><use href="#tick-red"/></svg>Installation</li>
      <li><svg class="tick"><use href="#tick-red"/></svg>Rebuilds</li>
    </ul>
    <ul class="abs hero-list right">
      <li><svg class="tick"><use href="#tick-red"/></svg>Preventive Maintenance Services</li>
      <li><svg class="tick"><use href="#tick-red"/></svg>OSHA Inspection</li>
    </ul>

    <div class="abs equip-fold"></div>
    <section class="abs equip-box">
      <h2>Hot &amp; Cold Equipment Services</h2>
      <ul class="equip-list">
        <li><svg class="tick"><use href="#tick-cyan"/></svg>Installation, Repair &amp; Rebuilds</li>
        <li><svg class="tick"><use href="#tick-cyan"/></svg>Preventive Maintenance Programs</li>
        <li><svg class="tick"><use href="#tick-cyan"/></svg>Equipment Cleaning &amp; Refurbishing</li>
        <li><svg class="tick"><use href="#tick-cyan"/></svg>OEM Parts with 30-Day Warranty</li>
        <li><svg class="tick"><use href="#tick-cyan"/></svg>Used Equipment Sales &amp; Rentals</li>
        <li><svg class="tick"><use href="#tick-cyan"/></svg>CKTA-Certified Technicians</li>
      </ul>
    </section>

    <h2 class="abs section-title support-title"><span class="accent">Full</span> Facility Support</h2>
    <ul class="abs check-list support-list">
      <li><svg class="tick"><use href="#tick-red"/></svg>Emergency Repairs (24/7 Availability)</li>
      <li><svg class="tick"><use href="#tick-red"/></svg>OSHA Inspections</li>
      <li><svg class="tick"><use href="#tick-red"/></svg>Handyman Services</li>
      <li><svg class="tick"><use href="#tick-red"/></svg>Electrical Upgrades (Licensed Contractor)</li>
      <li><svg class="tick"><use href="#tick-red"/></svg>Wall, Floor &amp; Ceiling Repairs</li>
      <li><svg class="tick"><use href="#tick-red"/></svg>Painting, Drywall, Door Closers</li>
      <li><svg class="tick"><use href="#tick-red"/></svg>Restaurant Furniture Repair/Replacement</li>
      <li><svg class="tick"><use href="#tick-red"/></svg>Décor, Signage, Parking Lot &amp; Dumpster Area Repairs</li>
      <li><svg class="tick"><use href="#tick-red"/></svg>Food Service Truck Equipment Repairs</li>
    </ul>

    <div class="abs badge-plain badge-a"></div>
    <div class="abs badge-plain badge-b"></div>

    <div class="abs photo photo-fryers" role="img" aria-label="Photo of a commercial fryer station"></div>
    <div class="abs photo photo-chefs" role="img" aria-label="Photo of chefs preparing food in a restaurant kitchen"></div>
    <div class="abs worker" role="img" aria-label="Photo of a repair technician in blue coveralls with a tool belt, pointing left"></div>

    <h2 class="abs section-title why-title"><span class="accent">Why</span> Choose Us?</h2>
    <ul class="abs check-list why-list left">
      <li><svg class="tick"><use href="#tick-red"/></svg>CKTA Certified Technicians</li>
      <li><svg class="tick"><use href="#tick-red"/></svg>OEM Parts for Maximum Reliability</li>
      <li><svg class="tick"><use href="#tick-red"/></svg>Preventive Maintenance<br>Subscribers Save on Labor Rates</li>
    </ul>
    <ul class="abs check-list why-list right">
      <li><svg class="tick"><use href="#tick-red"/></svg>Rapid Dispatch of Skilled Technicians</li>
      <li><svg class="tick"><use href="#tick-red"/></svg>Local &amp; Trusted in the Denver<br>Metro Area</li>
      <li><svg class="tick"><use href="#tick-red"/></svg>Graffiti Removal Services Available</li>
    </ul>

    <div class="abs footer-call">
      <div class="call-label">CALL TODAY FOR FAST, PROFESSIONAL SERVICE</div>
      <div class="call-number">
        <svg width="22" height="22" viewBox="0 0 24 24"><path d="M6.6 2.5l3 3.2-1.9 2.6c1.3 2.9 3.3 4.9 6.1 6.2l2.6-1.9 3.2 3-1.8 3.6c-8.2-.6-14-6.6-14.8-14.8z" fill="#e3191f"/></svg>
        033 555 019 4420
      </div>
    </div>
    <div class="abs divider one"></div>
    <div class="abs fix-all"><strong>WE FIX IT ALL</strong><span>IF YOU HAVE IT, WE PROBABLY FIX IT.</span></div>
    <div class="abs divider two"></div>
    <ul class="abs contact">
      <li><svg width="17" height="17" viewBox="0 0 20 20"><circle cx="10" cy="10" r="8.5" fill="none" stroke="#e3191f" stroke-width="1.8"/><path d="M1.5 10h17M10 1.5c-4 4.5-4 12.5 0 17M10 1.5c4 4.5 4 12.5 0 17" fill="none" stroke="#e3191f" stroke-width="1.5"/></svg>www.frontback.com</li>
      <li><svg width="17" height="17" viewBox="0 0 20 20"><rect x="1.5" y="4" width="17" height="12" fill="none" stroke="#e3191f" stroke-width="1.8"/><path d="M1.5 4.5l8.5 6.5 8.5-6.5" fill="none" stroke="#e3191f" stroke-width="1.6"/></svg>fix@frontback.com</li>
    </ul>
  </div>
</div>
</body>
</html>
```